Law Firm Website

We are a small California based law firm specializing in business, corporate and litigation matters. We need to have our website redesigned. We are looking for a new and fresh look for our site, keeping in mind that we are a law firm.
What we don't want:
**the traditional "gavel" and "scales of justice" look
**anything too crazy
What we do want:
**sophisticated yet modern and fresh corporate look and feel
**samples of websites we really like:
http://www.tarnwellhope.example
http://www.marrowgate.example/
we also like:
http://www.fenwoodastley.example/
http://www.qz.example/
http://www.brenhollow.example/
http://www.pvdn.example
http://www.nqrlaw.example/
The content will be whatever is currently on our website (www.okabelawgroup.example). We will be selecting the winner based on originality and keeping the above requirements in mind. Please note that the photos that you use will be the ones that we will be using, so choose wisely because the photos will make a difference.
Target Market(s)
Corporate clients
Industry/Entity Type
Law Firm
Look and feel

```html
<!DOCTYPE html>
<html lang="en">
<head>
<meta charset="utf-8">
<title>Okabe Law Group, LLP</title>
<link rel="stylesheet" href="https://fonts.googleapis.com/css2?family=Open+Sans:wght@300;400;600;700&family=Tinos:wght@400&display=swap">
<style>
  :root {
    --brand-blue: #0f6ab8;
    --brand-blue-dark: #0a4f95;
    --brand-blue-light: #1d8ae0;
    --heading-blue: #1670b6;
    --page-grey: #f1f1f1;
    --footer-grey: #ececec;
    --text-body: #575757;
    --text-muted: #8a8a8a;
    --text-dark: #4a4a4a;
    --nav-text: #4f4f4f;
    --white: #ffffff;
  }
  * { box-sizing: border-box; margin: 0; padding: 0; }
  html, body { width: 1200px; height: 1136px; overflow: hidden; }
  body {
    position: relative;
    background: linear-gradient(to bottom, var(--page-grey) 0, var(--page-grey) 515px, var(--white) 515px);
    font-family: "Open Sans", Arial, sans-serif;
    font-weight: 300;
    color: var(--text-body);
  }
  .serif { font-family: "Tinos", "Times New Roman", serif; font-weight: 400; }
  .abs { position: absolute; }

  /* Header */
  .brand-mark { left: 193px; top: 18px; width: 90px; height: 90px; background: var(--brand-blue-light); }
  .brand-name { left: 120px; top: 114px; width: 234px; text-align: center; font-size: 19px; color: var(--text-dark); }
  .brand-tagline { left: 120px; top: 139px; width: 234px; text-align: center; font-size: 9px; letter-spacing: 5px; color: var(--text-dark); font-weight: 400; }

  .search { left: 809px; top: 43px; width: 260px; height: 34px; background: #f7f7f7; border: 1px solid #e0e0e0; }
  .search span { position: absolute; left: 9px; top: 7px; font-size: 14px; color: #9a9a9a; font-weight: 400; }
  .search svg { position: absolute; right: 8px; top: 7px; }

  .main-nav a { position: absolute; top: 124px; font-size: 19px; color: var(--nav-text); text-decoration: none; }
  .main-nav .active { left: 582px; top: 110px; width: 90px; height: 50px; padding-top: 14px; text-align: center; color: var(--white);
    background: linear-gradient(to bottom, var(--brand-blue-light), var(--brand-blue-dark)); }
  .nav-rule { left: 120px; top: 160px; width: 960px; height: 5px; background: var(--brand-blue-dark); }

  /* Hero */
  .hero-photo { left: 120px; top: 165px; width: 960px; height: 442px;
    background: linear-gradient(100deg, #b9ad98 0%, #e3d8c3 25%, #cfc2ab 45%, #eae0cf 60%, #c7baa3 80%, #a89c88 100%); }
  .hero-caption { left: 690px; top: 271px; width: 380px; height: 244px; background: rgba(60,60,60,0.72); padding: 24px 30px; color: var(--white); }
  .hero-caption h2 { font-size: 26px; margin-bottom: 8px; }
  .hero-caption p { font-size: 14px; line-height: 24px; font-weight: 300; }
  .btn { display: inline-block; margin-top: 18px; width: 109px; height: 33px; line-height: 33px; text-align: center; font-size: 15px; color: var(--white);
    background: linear-gradient(to bottom, var(--brand-blue-light), var(--brand-blue-dark)); }
  .slider-dots { left: 965px; top: 558px; display: flex; gap: 8px; }
  .slider-dots i { width: 14px; height: 14px; background: var(--white); }
  .slider-dots i.on { background: var(--brand-blue); }

  /* Content */
  .section-title { font-size: 26px; color: var(--heading-blue); }
  .welcome-title { left: 120px; top: 632px; }
  .welcome-text { left: 120px; top: 691px; width: 552px; font-size: 14px; line-height: 26px; }
  .welcome-text p + p { margin-top: 26px; }

  .news-title { left: 690px; top: 632px; }
  .news-arrows { left: 1036px; top: 642px; }
  .news-item { left: 690px; width: 380px; }
  .news-thumb { position: absolute; left: 0; top: 0; width: 140px; height: 92px; }
  .news-body { position: absolute; left: 157px; top: 0; width: 228px; }
  .news-date { font-size: 18px; color: var(--text-dark); line-height: 22px; }
  .news-author { font-size: 14px; font-weight: 700; color: var(--text-dark); margin-top: 4px; }
  .news-text { font-size: 14px; line-height: 24px; color: var(--text-muted); margin-top: 6px; }

  /* Footer */
  .site-footer { left: 0; top: 1051px; width: 1200px; height: 85px; background: var(--footer-grey); }
  .footer-nav { left: 129px; top: 1073px; font-size: 14px; color: #666; font-weight: 400; display: flex; gap: 0; }
  .footer-nav span.sep { margin: 0 24px; }
  .copyright { left: 130px; top: 1101px; font-size: 14px; color: #666; font-weight: 400; }
  .social { left: 1026px; top: 1078px; display: flex; gap: 10px; }
  .social i { width: 20px; height: 20px; border-radius: 50%; background: var(--brand-blue); }
</style>
</head>
<body>
  <header>
    <div class="abs brand-mark" aria-hidden="true"></div>
    <div class="abs brand-name serif">Okabe Law Group, LLP</div>
    <div class="abs brand-tagline">ATTORNEY OF LAW</div>

    <div class="abs search">
      <span>Search</span>
      <svg width="20" height="18" viewBox="0 0 20 18" aria-hidden="true">
        <circle cx="7" cy="7" r="5.5" fill="none" stroke="#b5b5b5" stroke-width="2"/>
        <line x1="11" y1="11" x2="18" y2="16" stroke="#b5b5b5" stroke-width="3" stroke-linecap="round"/>
      </svg>
    </div>

    <nav class="main-nav serif">
      <a class="active" href="#">Home</a>
      <a style="left:679px" href="#">About OLG</a>
      <a style="left:789px" href="#">Practice Areas</a>
      <a style="left:924px" href="#">Links</a>
      <a style="left:985px" href="#">Contact Us</a>
    </nav>
    <div class="abs nav-rule"></div>
  </header>

  <section>
    <div class="abs hero-photo" role="img" aria-label="Photo of stone columns of a classical courthouse colonnade"></div>
    <div class="abs hero-caption">
      <h2 class="serif">Okabe Law Group</h2>
      <p>Lorem Ipsum is simply dummy text of the printing and typesetting industry. Lorem Ipsum has been the industry's standard dummy text ever since the 1500s, when an unknown printer took a galley of type and scrambled</p>
      <span class="btn serif">Read More</span>
    </div>
    <div class="abs slider-dots"><i class="on"></i><i></i><i></i><i></i></div>
  </section>

  <main>
    <h1 class="abs section-title serif welcome-title">Welcome to Okabe Law Group, LLP</h1>
    <div class="abs welcome-text">
      <p>Okabe Law Group, LLP provides quality legal representation to corporate as well as individual clients in the areas of business, corporate, securities, products liability, civil litigation (in State and Federal Courts), Alternative Dispute Resolution (arbitration and mediation), as well as a host of transactional matters.Our attorneys are committed to providing zealous advocacy in litigation, as well as creative approaches to difficult challenges that face our business clients. Our goal is to provide the highest level of representation and personal service to each and every client, and to meet and exceed each client's expectations. We take the time to explore and explain all viable options and keep our clients informed at every step of their legal matter.</p>
      <p>We encourage you to contact us to discuss the development of a professional relationship. If you seek a firm that is experienced and committed to representing your best interests, then look no further.</p>
    </div>

    <h2 class="abs section-title serif news-title">Latest News</h2>
    <svg class="abs news-arrows" width="36" height="22" viewBox="0 0 36 22" aria-hidden="true">
      <polyline points="11,2 3,11 11,20" fill="none" stroke="var(--brand-blue)" stroke-width="3"/>
      <polyline points="25,2 33,11 25,20" fill="none" stroke="var(--brand-blue)" stroke-width="3"/>
    </svg>

    <article class="abs news-item" style="top:695px">
      <div class="news-thumb" role="img" aria-label="Photo of a white office tower under blue sky" style="background:linear-gradient(to bottom,#2f6fb8 0%,#7aa6d8 45%,#d8d8d4 60%,#4d6a3c 85%,#3a3a3a 100%)"></div>
      <div class="news-body">
        <div class="news-date">6-2-2014</div>
        <div class="news-author">Posted By : Admin</div>
        <div class="news-text">Lorem Ipsum is simply dummy text of the printing and typesetting industry. Lorem Ipsum has been the industry's standard</div>
      </div>
    </article>

    <article class="abs news-item" style="top:871px">
      <div class="news-thumb" role="img" aria-label="Photo of an office building with palm trees" style="background:linear-gradient(to bottom,#3f82cc 0%,#9cc0e4 40%,#7f9a5e 65%,#e6e6e2 100%)"></div>
      <div class="news-body">
        <div class="news-date">6-2-2014</div>
        <div class="news-author">Posted By : Admin</div>
        <div class="news-text">Lorem Ipsum is simply dummy text of the printing and typesetting industry. Lorem Ipsum has been the industry's standard</div>
      </div>
    </article>
  </main>

  <footer>
    <div class="abs site-footer"></div>
    <nav class="abs footer-nav">
      <span>Home</span><span class="sep">|</span>
      <span>About OLG</span><span class="sep">|</span>
      <span>Practice Areas</span><span class="sep">|</span>
      <span>Links</span><span class="sep">|</span>
      <span>Contact Us</span>
    </nav>
    <div class="abs copyright">© 2014 Company Name ,All Rights Reserved</div>
    <div class="abs social" aria-label="Social media links"><i></i><i></i></div>
  </footer>
</body>
</html>
```